Canadian Christian Church needs design for new sermon series

A graphic design for our series and an invitation card to invite people to the series. Check design brief for more detailed information. Target audience: young families and young adults. Looking for a creative design that will get people's attention and create interest. See design brief for copy of design purchased for previous series.
Updates
entered Apr 4 incorrectly. Need a week to receive and review designs, and today is Apr 2/19. Thanks!
Target Market(s)
young families and young adults
Colors
Designer to choose colors to be used in the design.
Look and feel

```html
<!DOCTYPE html>
<html lang="en">
<head>
<meta charset="utf-8">
<title>Messy – Sermon Series Invitation Card</title>
<link rel="stylesheet" href="https://fonts.googleapis.com/css2?family=Anton&family=Roboto+Slab:wght@400;700&family=Montserrat:wght@400;600;700&family=Roboto+Condensed:wght@400&display=swap">
<style>
  :root{
    --bg:#e6e6e6;
    --ink:#2d2a27;
    --orange:#f39a1e;
    --purple:#9c2a9c;
    --blue:#1f7fd0;
    --cream:#cfc8b2;
    --cream-light:#e2ddcd;
    --footer:#3b3532;
    --tick:#1f6fc0;
  }
  *{box-sizing:border-box;margin:0;padding:0}
  html,body{width:1200px;height:903px;overflow:hidden;background:var(--bg)}
  body{position:relative;font-family:"Montserrat",sans-serif;color:var(--ink)}

  .card{position:absolute;width:560px;height:440px;overflow:hidden;box-shadow:0 2px 8px rgba(0,0,0,.18)}
  .card--front{left:25px;top:231px;background:#111}
  .card--back{left:615px;top:231px;background:radial-gradient(ellipse at 75% 45%,var(--cream-light),var(--cream) 70%)}

  /* front */
  .hero-photo{position:absolute;inset:0;width:100%;height:100%}
  .brand{position:absolute;left:0;right:0;top:24px;text-align:center}
  .brand__dot{width:62px;height:62px;border-radius:50%;background:var(--orange);margin:0 auto 10px}
  .brand__name{font-family:"Roboto Slab",serif;font-size:15px;color:#1c1c1c}
  .series-title{position:absolute;left:0;right:0;top:262px;text-align:center;font-family:"Anton",sans-serif;font-size:74px;line-height:1;color:var(--orange);-webkit-text-stroke:2px var(--purple);letter-spacing:1px}
  .series-tagline{position:absolute;left:0;right:0;top:342px;text-align:center;font-family:"Roboto Slab",serif;font-size:39px;line-height:1.15;color:var(--purple)}
  .series-rule{position:absolute;left:30px;right:30px;top:390px;height:1px;background:rgba(255,255,255,.25)}
  .series-audience{position:absolute;left:0;right:0;top:396px;text-align:center;font-family:"Roboto Slab",serif;font-weight:700;font-size:23px;line-height:1.2;color:var(--blue);white-space:nowrap}

  /* back */
  .services-heading{position:absolute;left:0;width:560px;top:26px;text-align:center;font-family:"Roboto Slab",serif;font-weight:700;line-height:1.15}
  .services-heading__label{font-size:29px;display:block}
  .services-heading__time{font-size:30px;display:block}
  .info{position:absolute;left:30px;top:122px;font-size:13px;line-height:17px}
  .info h3{font-size:13.5px;font-weight:700;margin-bottom:2px}
  .info ul{list-style:none;margin-bottom:7px}
  .info li{display:flex;align-items:center;gap:6px;white-space:nowrap}
  .info li b{font-weight:600}
  .tick{width:9px;height:9px;flex:none}
  .values-diagram{position:absolute;left:342px;top:110px;width:200px;height:200px}
  .contact-bar{position:absolute;left:0;bottom:14px;width:350px;height:68px;background:var(--footer);color:#fff;font-family:"Roboto Condensed",sans-serif;font-size:11.5px;padding:9px 0 0 30px;line-height:18px;white-space:nowrap}
  .contact-bar .row{display:flex;align-items:center;gap:5px}
  .contact-bar .row--plain{display:block}
  .contact-bar svg{width:10px;height:10px;flex:none}
  .contact-bar a{color:var(--orange);text-decoration:none}
  .back-brand{position:absolute;right:28px;bottom:26px;text-align:center}
  .back-brand__dot{width:66px;height:66px;border-radius:50%;background:var(--orange);margin:0 auto 6px}
  .back-brand__name{font-family:"Roboto Slab",serif;font-size:14px;white-space:nowrap}
</style>
</head>
<body>

<section class="card card--front" aria-label="Series invitation, front">
  <svg class="hero-photo" role="img" aria-label="Photo: silhouette of a family holding hands on a beach at sunset" viewBox="0 0 560 440" preserveAspectRatio="none">
    <defs>
      <linearGradient id="sunset" x1="0" y1="0" x2="0" y2="1">
        <stop offset="0" stop-color="#e5a066"/>
        <stop offset=".3" stop-color="#d98a6e"/>
        <stop offset=".5" stop-color="#b8716a"/>
        <stop offset=".65" stop-color="#5a4046"/>
        <stop offset=".8" stop-color="#1e1a1e"/>
        <stop offset="1" stop-color="#0e0e12"/>
      </linearGradient>
    </defs>
    <rect width="560" height="440" fill="url(#sunset)"/>
  </svg>

  <div class="brand">
    <div class="brand__dot"></div>
    <p class="brand__name">Maple Grove Family Church</p>
  </div>
  <h1 class="series-title">MESSY</h1>
  <p class="series-tagline">Joining God in the Mess</p>
  <div class="series-rule"></div>
  <p class="series-audience">CONNECTING YOUNG FAMILIES TO CHRIST</p>
</section>

<section class="card card--back" aria-label="Series invitation, back">
  <h2 class="services-heading">
    <span class="services-heading__label">THE TIME OF THE SERVICES:</span>
    <span class="services-heading__time">Sundays @ 10:30</span>
  </h2>

  <div class="info">
    <h3>Names &amp; Dates of the sermons:</h3>
    <ul>
      <li><svg class="tick" viewBox="0 0 10 10"><circle cx="5" cy="5" r="5" fill="var(--tick)"/><path d="M2.8 5.2l1.5 1.5 3-3" stroke="#fff" stroke-width="1.3" fill="none"/></svg><span><b>April 28th:</b> “We Made This Mess”</span></li>
      <li><svg class="tick" viewBox="0 0 10 10"><circle cx="5" cy="5" r="5" fill="var(--tick)"/><path d="M2.8 5.2l1.5 1.5 3-3" stroke="#fff" stroke-width="1.3" fill="none"/></svg><span><b>May 5th:</b> “Bless in the Mess”</span></li>
      <li><svg class="tick" viewBox="0 0 10 10"><circle cx="5" cy="5" r="5" fill="var(--tick)"/><path d="M2.8 5.2l1.5 1.5 3-3" stroke="#fff" stroke-width="1.3" fill="none"/></svg><span><b>May 12th:</b> “Born into the Mess”</span></li>
      <li><svg class="tick" viewBox="0 0 10 10"><circle cx="5" cy="5" r="5" fill="var(--tick)"/><path d="M2.8 5.2l1.5 1.5 3-3" stroke="#fff" stroke-width="1.3" fill="none"/></svg><span><b>May 19th:</b> “Messy Work”</span></li>
      <li><svg class="tick" viewBox="0 0 10 10"><circle cx="5" cy="5" r="5" fill="var(--tick)"/><path d="M2.8 5.2l1.5 1.5 3-3" stroke="#fff" stroke-width="1.3" fill="none"/></svg><span><b>May 26th:</b> “Messy Church”</span></li>
      <li><svg class="tick" viewBox="0 0 10 10"><circle cx="5" cy="5" r="5" fill="var(--tick)"/><path d="M2.8 5.2l1.5 1.5 3-3" stroke="#fff" stroke-width="1.3" fill="none"/></svg><span><b>June 2nd:</b> “Messy Hospitality”</span></li>
      <li><svg class="tick" viewBox="0 0 10 10"><circle cx="5" cy="5" r="5" fill="var(--tick)"/><path d="M2.8 5.2l1.5 1.5 3-3" stroke="#fff" stroke-width="1.3" fill="none"/></svg><span><b>June 9th:</b> TBD</span></li>
      <li><svg class="tick" viewBox="0 0 10 10"><circle cx="5" cy="5" r="5" fill="var(--tick)"/><path d="M2.8 5.2l1.5 1.5 3-3" stroke="#fff" stroke-width="1.3" fill="none"/></svg><span><b>June 16th:</b> “Messy within Boundaries”</span></li>
    </ul>
    <h3>Features of the service:</h3>
    <ul>
      <li><svg class="tick" viewBox="0 0 10 10"><circle cx="5" cy="5" r="5" fill="var(--tick)"/><path d="M2.8 5.2l1.5 1.5 3-3" stroke="#fff" stroke-width="1.3" fill="none"/></svg><span>Staffed nursery &amp; children’s program every Sunday</span></li>
      <li><svg class="tick" viewBox="0 0 10 10"><circle cx="5" cy="5" r="5" fill="var(--tick)"/><path d="M2.8 5.2l1.5 1.5 3-3" stroke="#fff" stroke-width="1.3" fill="none"/></svg><span>Coffee &amp; snacks</span></li>
      <li><svg class="tick" viewBox="0 0 10 10"><circle cx="5" cy="5" r="5" fill="var(--tick)"/><path d="M2.8 5.2l1.5 1.5 3-3" stroke="#fff" stroke-width="1.3" fill="none"/></svg><span>Everyone welcome</span></li>
    </ul>
  </div>

  <svg class="values-diagram" role="img" aria-label="Illustration: interlocking ribbon diagram of the church's core values" viewBox="0 0 200 200">
    <defs>
      <linearGradient id="ribbon" x1="0" y1="0" x2="1" y2="1">
        <stop offset="0" stop-color="#1f6fc0"/>
        <stop offset=".5" stop-color="#f39a1e"/>
        <stop offset="1" stop-color="#8e2a9e"/>
      </linearGradient>
    </defs>
    <circle cx="100" cy="100" r="96" fill="url(#ribbon)" opacity=".85"/>
  </svg>

  <div class="contact-bar">
    <div class="row"><svg viewBox="0 0 10 10"><path d="M5 1a3 3 0 0 1 3 3c0 2.2-3 5-3 5S2 6.2 2 4a3 3 0 0 1 3-3z" fill="none" stroke="var(--orange)" stroke-width="1.2"/><circle cx="5" cy="4" r="1" fill="var(--orange)"/></svg>1820 Cedar Line East Oakridge, ON L4A 2B3</div>
    <div class="row"><svg viewBox="0 0 10 10"><path d="M2 1l2 2-1 1.3a6 6 0 0 0 2.7 2.7L7 6l2 2-1.3 1.3C4.5 9 1 5.5.7 2.3z" fill="var(--orange)"/></svg>905-555-0142&nbsp;&nbsp;<svg viewBox="0 0 10 10"><circle cx="5" cy="5" r="4.2" fill="none" stroke="var(--orange)" stroke-width="1.1"/><path d="M1 5h8M5 .8c2 2.5 2 5.9 0 8.4M5 .8c-2 2.5-2 5.9 0 8.4" fill="none" stroke="var(--orange)" stroke-width=".9"/></svg>www.maplegrovechurch.ca</div>
    <div class="row--plain">Please contact Laura Bennett <a href="mailto:worship@maplegrovechurch.ca">worship@maplegrovechurch.ca</a></div>
  </div>

  <div class="back-brand">
    <div class="back-brand__dot"></div>
    <p class="back-brand__name">Maple Grove Family Church</p>
  </div>
</section>

</body>
</html>
```